Advertising company unique advertising platform

we need a logo design for a new company based in Australia Melbourne. We develop innovated advertising platform where consumer can use this platform to get regular discount, as business owner they can use this platform for free advertisement. Payment for this advertisement platform only payable every two weeks, when I generate revenue for their business

Industry/Entity Type

Advertising

Contact Information for Business Card

Dale Morven | Co-Founder |Managing Director
Suite 718 240 Wattlebrook Lane Melbourne Vic 3000

ABN 38 614 207 923
Tel: +61 0487 259 318 | Email: dale.morven@plivorantu.com

Font styles to use
Decorative
Script

Requirements
Must have
• Try few different design and some round corner business card
Should not have
• One round corner business card...try 4 different colour background not only black, make sure two side is designed. Be creative so imagine you are giving this to a client make sure has wow factor, if you can also try one design with engrave like all the logo, words look 3d feel
• The word Advertising Platform use attached file font

```html
<!DOCTYPE html>
<html lang="en">
<head>
<meta charset="utf-8">
<title>Halvo Market – Business Card</title>
<link rel="stylesheet" href="https://fonts.googleapis.com/css2?family=Ubuntu:wght@400;500;700&display=swap">
<style>
  :root {
    --backdrop: #2b2b2b;
    --card-dark: #242424;
    --card-light: #f7f7f7;
    --flame-deep: #e8452c;
    --flame-warm: #f7a53a;
    --name-red: #e8452c;
    --title-teal: #17dcae;
    --body-grey: #4a4a4a;
  }
  * { margin: 0; padding: 0; box-sizing: border-box; }
  html, body { width: 1200px; height: 886px; overflow: hidden; }
  body {
    background: var(--backdrop);
    font-family: "Ubuntu", sans-serif;
    position: relative;
  }
  .card {
    position: absolute;
    width: 560px;
    height: 320px;
    border-radius: 26px;
    overflow: hidden;
  }
  /* Back side */
  .card-back {
    left: 60px;
    top: 110px;
    background: var(--card-dark);
  }
  .brand {
    position: absolute;
    left: 0; right: 0; top: 110px;
    display: flex;
    align-items: center;
    justify-content: center;
    gap: 16px;
  }
  .brand-dot {
    width: 56px; height: 56px;
    border-radius: 50%;
    background: var(--flame-deep);
  }
  .brand-name {
    color: var(--flame-warm);
    font-weight: 700;
    font-size: 40px;
  }
  .website {
    position: absolute;
    left: 0; right: 0; top: 232px;
    text-align: center;
    color: var(--flame-warm);
    font-size: 15px;
    letter-spacing: 5px;
  }
  /* Front side */
  .card-front {
    left: 580px;
    top: 456px;
    background: var(--card-light);
  }
  .front-art { position: absolute; inset: 0; }
  .front-brand {
    position: absolute;
    left: 62px; top: 162px;
    width: 140px;
    text-align: center;
    color: var(--flame-deep);
    font-weight: 700;
    font-size: 20px;
  }
  .contact {
    position: absolute;
    left: 290px; top: 56px;
  }
  .contact-name {
    color: var(--name-red);
    font-weight: 700;
    font-size: 21px;
  }
  .contact-role {
    color: var(--title-teal);
    font-weight: 500;
    font-size: 15px;
    line-height: 1.2;
    margin-top: 4px;
  }
  .contact-details {
    margin-top: 22px;
    color: var(--body-grey);
    font-size: 13.5px;
    line-height: 1.35;
    list-style: none;
  }
  .contact-details .icon-line {
    display: flex; align-items: center; gap: 8px;
  }
  .contact-details svg { width: 12px; height: 12px; fill: var(--name-red); flex: none; }
</style>
</head>
<body>

<section class="card card-back">
  <div class="brand">
    <span class="brand-dot"></span>
    <span class="brand-name">Halvo Market</span>
  </div>
  <p class="website">www.plivorantu.com</p>
</section>

<section class="card card-front">
  <svg class="front-art" viewBox="0 0 560 320" preserveAspectRatio="none">
    <defs>
      <linearGradient id="bandGradient" x1="0" y1="0" x2="0" y2="1">
        <stop offset="0" stop-color="var(--flame-warm)"/>
        <stop offset="1" stop-color="var(--flame-deep)"/>
      </linearGradient>
    </defs>
    <path d="M0 0 H240 C190 90 200 200 140 320 H0 Z" fill="var(--card-dark)"/>
    <path d="M240 0 H262 C216 100 226 210 168 320 H140 C200 200 190 90 240 0 Z" fill="url(#bandGradient)"/>
    <circle cx="132" cy="175" r="86" fill="var(--card-light)"/>
  </svg>
  <div class="front-brand">Halvo Market</div>
  <div class="contact">
    <h1 class="contact-name">DALE MORVEN</h1>
    <p class="contact-role">CO-FOUNDER<br>MANAGING DIRECTOR</p>
    <ul class="contact-details">
      <li>Plivorantu</li>
      <li>ABN 38 614 207 923</li>
      <li>Suite 718 240 Wattlebrook Lane</li>
      <li>Melbourne Vic 3000</li>
      <li class="icon-line">
        <svg viewBox="0 0 24 24"><path d="M6.6 10.8a15 15 0 0 0 6.6 6.6l2.2-2.2a1 1 0 0 1 1-.25 11.4 11.4 0 0 0 3.6.57 1 1 0 0 1 1 1V20a1 1 0 0 1-1 1A17 17 0 0 1 3 4a1 1 0 0 1 1-1h3.5a1 1 0 0 1 1 1c0 1.25.2 2.45.57 3.57a1 1 0 0 1-.25 1z"/></svg>
        +61 0487 259 318
      </li>
      <li class="icon-line">
        <svg viewBox="0 0 24 24"><path d="M2 5h20v14H2z M2 5l10 8 10-8" /></svg>
        dale.morven@plivorantu.com
      </li>
    </ul>
  </div>
</section>

</body>
</html>
```